Re-Design an adult education portal

I need support to re-design an adult education portal. Currently the customer has an incomplete website which should be prepared in a new format.
I have the idea how to realize, but I have no clue how to design it. The hard thing is to have a "beautiful" website with available logo and main color. I hope you can support me.

Name of Website: moluvo (moluvo.ch)
Content: adult eduction for adult in safety at work, mountain climbing, dog school. various courses in different areas. But on old webpage is hard to find the different possibilities.
main color: Ral 6011 (green) -> #6C7C59
logo: you see on top of website the logo (2 dogs and a mountain with a colour gradient).

new website: for new webpage I decided to have a navigation for each section of education. In the main area I would like to have some pictures to give an idea what content is behind. At the moment it looks terrible, so I decided to use you as support for me to make the webpage prettier :). And maybe you have an better idea how to make it great. -> current state of new web page: https://moluvo.perch-net.ch/

Target Market(s)

adult eduction for adult in safety at work, mountain climbing, dog school

Number of Pages Required

1 page

Font styles to use
Serif
Sans Serif

Requirements
Must have
• As main color is set "Ral 6011" (green) -> #6C7C59

```html
<!DOCTYPE html>
<html lang="en">
<head>
<meta charset="utf-8">
<title>moluvo – adult education</title>
<link rel="stylesheet" href="https://fonts.googleapis.com/css2?family=Josefin+Sans:wght@300;400;600;700&display=swap">
<style>
:root{
  --green:#6c7c59;
  --dark:#1f1f1f;
  --black:#0b0b0b;
  --ink:#333;
  --muted:#6a6a6a;
  --soft:#f3f3f3;
  --white:#fff;
  --line:#e2e2e2;
}
*{box-sizing:border-box;margin:0;padding:0}
html,body{width:1200px;height:4181px;overflow:hidden}
body{font-family:"Josefin Sans",sans-serif;color:var(--ink);background:var(--white);position:relative}
.abs{position:absolute}
.btn{position:absolute;display:flex;align-items:center;justify-content:center;border-radius:20px;color:#fff;font-size:10px;font-weight:600;letter-spacing:.3px;text-transform:uppercase}
.btn.dark{background:var(--dark)}
.btn.green{background:var(--green)}
.label{position:absolute;font-size:11px;text-transform:uppercase;color:var(--ink);letter-spacing:.2px}
.heading{position:absolute;color:var(--green);font-weight:400;line-height:1.3}
.copy{position:absolute;font-size:12px;line-height:21px;color:var(--muted);font-weight:300;text-align:justify}
.center{text-align:center}
.photo{position:absolute}

/* top bar */
.topbar{left:0;top:0;width:1200px;height:45px;background:var(--dark);color:#fff;font-size:11px}
.topbar span{position:absolute;top:17px;display:flex;align-items:center;gap:8px}
.topbar .social{position:absolute;left:905px;top:0;width:295px;height:45px;background:var(--green);border-radius:22px 0 0 22px;display:flex;align-items:center;padding-left:46px;gap:14px}
.dot{width:12px;height:12px;border:1.5px solid #fff;border-radius:50%}

/* nav */
.nav{left:0;top:45px;width:1200px;height:67px;background:#fff;border-bottom:1px solid var(--line)}
.logo{position:absolute;display:flex;align-items:center;gap:6px;font-size:20px;font-weight:600;color:var(--green)}
.logo i{width:10px;height:10px;background:var(--green);display:block}
.menu{position:absolute;left:297px;top:28px;display:flex;gap:22px;font-size:11px;color:var(--ink)}

/* hero */
.hero{left:0;top:112px;width:1200px;height:429px;background:linear-gradient(180deg,#8c9aa6 0%,#aab5bd 45%,#c9d0d3 100%)}
.hero h1{position:absolute;left:300px;top:128px;width:600px;text-align:center;color:#fff;font-weight:300;font-size:33px;line-height:45px}
.hero h1 b{font-weight:600;color:var(--dark)}
.arrow{position:absolute;width:38px;height:38px;border-radius:50%}

/* cards */
.card{position:absolute;background:#fff;border:1px solid var(--line);border-radius:4px}
.card.active{background:var(--green);border-color:var(--green);color:#fff}
.card-title{position:absolute;width:100%;text-align:center;font-size:17px;line-height:23px;color:var(--dark)}
.card.active .card-title,.card.active .card-body{color:#fff}
.card-body{position:absolute;width:100%;text-align:center;font-size:10.5px;line-height:18px;color:var(--muted);padding:0 20px}
.icon-ring{position:absolute;width:58px;height:58px;border-radius:50%;background:#fff;box-shadow:0 2px 6px rgba(0,0,0,.15);display:flex;align-items:center;justify-content:center}

.news{position:absolute;top:3225px;width:272px;height:294px;background:#fff;box-shadow:0 2px 10px rgba(0,0,0,.12);border-radius:3px}
.news-title{position:absolute;top:164px;width:100%;text-align:center;color:var(--green);font-size:12.5px;font-weight:600}
.news-meta{position:absolute;top:186px;width:100%;text-align:center;font-size:10px;color:var(--muted)}
.news-body{position:absolute;top:208px;width:100%;padding:0 30px;text-align:center;font-size:9.5px;line-height:14px;color:var(--muted)}

.foot h4{position:absolute;top:3924px;color:var(--green);font-size:14px;font-weight:600}
.foot ul{position:absolute;top:3958px;list-style:none;font-size:11px;line-height:24px;color:var(--ink)}
</style>
</head>
<body>

<!-- top bar -->
<header class="abs topbar">
  <span style="left:162px"><svg width="12" height="12" viewBox="0 0 12 12"><rect x="1" y="1" width="10" height="8" rx="1" fill="none" stroke="#fff"/><path d="M3 9v2l2-2" fill="none" stroke="#fff"/></svg>Are you interested in Life Coaching</span>
  <span style="left:634px"><svg width="12" height="10" viewBox="0 0 12 10"><rect x=".5" y=".5" width="11" height="9" fill="none" stroke="#fff"/><path d="M.5 .5l5.5 5 5.5-5" fill="none" stroke="#fff"/></svg>info@moluvo.ch</span>
  <span style="left:757px"><svg width="8" height="12" viewBox="0 0 8 12"><rect x=".5" y=".5" width="7" height="11" rx="1" fill="none" stroke="#fff"/></svg>+41 79 512 48 30</span>
  <div class="social"><i class="dot"></i><i class="dot"></i><i class="dot"></i><i class="dot"></i></div>
</header>

<!-- navigation -->
<nav class="abs nav">
  <div class="logo" style="left:162px;top:22px"><i></i>moluvo.ch</div>
  <div class="menu">
    <span>Home</span><span>Occupational safety ▾</span><span>First Aid ▾</span><span>Dog School ▾</span><span>CZV ▾</span><span>Mountain Training ▾</span><span>About moluvo ▾</span>
  </div>
  <div class="btn dark" style="left:898px;top:13px;width:141px;height:41px">Learn course now!</div>
</nav>

<!-- hero -->
<section class="abs hero" role="img" aria-label="Child on a ladder reaching into a cloudy sky">
  <div class="abs center" style="left:300px;top:104px;width:600px;color:#fff;font-size:10px;text-transform:uppercase">Your training and course partner</div>
  <h1>We offer <b>training tailored</b> to your <b>needs,</b> target-oriented and tailored to <b>your skills</b> and knowledge.</h1>
  <div class="btn dark" style="left:525px;top:294px;width:151px;height:33px">Learn course now!</div>
  <div class="arrow" style="left:25px;top:195px;border:1.5px solid #fff"><svg width="35" height="35" viewBox="0 0 35 35"><path d="M20 11l-6 6.5 6 6.5" fill="none" stroke="#fff" stroke-width="1.5"/></svg></div>
  <div class="arrow" style="left:1139px;top:195px;background:var(--green)"><svg width="38" height="38" viewBox="0 0 38 38"><path d="M17 13l6 6-6 6" fill="none" stroke="#fff" stroke-width="1.5"/></svg></div>
</section>

<!-- who we are -->
<section class="abs" style="left:0;top:541px;width:1200px;height:633px;background:var(--soft)">
  <svg class="abs" style="left:162px;top:92px" width="497" height="453" viewBox="0 0 497 453">
    <polygon points="0,421 497,344 497,372 0,453" fill="var(--green)"/>
  </svg>
  <div class="photo" style="left:162px;top:92px;width:496px;height:415px;background:linear-gradient(160deg,#e8ecef,#9aa3a8 55%,#5d6468);clip-path:polygon(0 0,100% 0,100% 82%,0 100%)" role="img" aria-label="Hiker standing on a snowy mountain slope"></div>
  <div class="label" style="left:690px;top:103px">Who we are</div>
  <div class="heading" style="left:690px;top:130px;width:349px;font-size:26px;line-height:36px;text-align:justify">Lorem ipsum dolor sit amet, consectetur adipiscing.</div>
  <p class="copy" style="left:690px;top:214px;width:349px">Lorem ipsum dolor sit amet, consectetur adipiscing elit. Etiam sollicitudin ante in purus viverra, vitae tempor lorem laoreet. Vestibulum feugiat, ipsum a euismod finibus, massa nisl tristique lacus, eget pellentesque urna metus a turpis. Nullam eget feugiat enim.</p>
  <p class="copy" style="left:690px;top:344px;width:349px">Lorem ipsum dolor sit amet, consectetur adipiscing elit. Etiam sollicitudin ante in purus viverra, vitae tempor lorem laoreet. Vestibulum feugiat, ipsum a euismod finibus, massa nisl tristique lacus, eget pellentesque urna metus a turpis.</p>
  <div class="btn dark" style="left:690px;top:466px;width:115px;height:32px">Read more</div>
  <div class="label" style="left:840px;top:466px">Call to ask any question</div>
  <div class="abs" style="left:840px;top:484px;font-size:23px;color:var(--green);font-weight:600">+41 79 512 48 30</div>
</section>

<!-- courses -->
<section class="abs" style="left:0;top:1174px;width:1200px;height:676px;background:#fff">
  <div class="label center" style="left:0;top:96px;width:1200px">Our courses</div>
  <div class="heading center" style="left:0;top:116px;width:1200px;font-size:29px">Explore How can We help you</div>
  <p class="copy center" style="left:400px;top:162px;width:400px;text-align:center;line-height:23px">Lorem ipsum dolor sit amet, consectetur adipiscing elit. Etiam sollicitudin ante in purus viverra, vitae tempor lorem laoreet.</p>
  <svg class="abs" style="left:92px;top:382px" width="28" height="40" viewBox="0 0 28 40"><path d="M22 2L4 20l18 18" fill="none" stroke="var(--dark)" stroke-width="2"/></svg>
  <svg class="abs" style="left:1081px;top:382px" width="28" height="40" viewBox="0 0 28 40"><path d="M6 2l18 18L6 38" fill="none" stroke="var(--green)" stroke-width="2"/></svg>
</section>

<div class="card" style="left:162px;top:1496px;width:272px;height:256px"><div class="card-title" style="top:128px">Lorem ipsum dolor sit amet,<br>consectetur adipiscing elit</div><div class="card-body" style="top:182px">Nunc aliquet nulla nec dapibus max imus. Nam aliquam neque.</div></div>
<div class="card active" style="left:466px;top:1496px;width:270px;height:256px"><div class="card-title" style="top:128px">Lorem ipsum dolor sit amet,<br>consectetur adipiscing elit</div><div class="card-body" style="top:182px">Nunc aliquet nulla nec dapibus max imus. Nam aliquam neque.</div></div>
<div class="card" style="left:767px;top:1496px;width:272px;height:256px"><div class="card-title" style="top:128px">Lorem ipsum dolor sit amet,<br>consectetur adipiscing elit</div><div class="card-body" style="top:182px">Nunc aliquet nulla nec dapibus max imus. Nam aliquam neque.</div></div>

<div class="photo" style="left:177px;top:1410px;width:240px;height:159px;background:linear-gradient(180deg,#b9bcbf,#8d9196 60%,#6d4c44)" role="img" aria-label="Worker operating a red forklift"></div>
<div class="photo" style="left:481px;top:1410px;width:240px;height:159px;background:linear-gradient(180deg,#b9bcbf,#8d9196 60%,#6d4c44)" role="img" aria-label="Worker operating a red forklift"></div>
<div class="photo" style="left:783px;top:1410px;width:240px;height:159px;background:linear-gradient(180deg,#b9bcbf,#8d9196 60%,#6d4c44)" role="img" aria-label="Worker operating a red forklift"></div>

<div class="icon-ring" style="left:269px;top:1540px"><svg width="30" height="30" viewBox="0 0 30 30" fill="none" stroke="var(--green)"><rect x="6" y="3" width="21" height="13"/><path d="M10 7h13M10 10h13M3 14l7-4M3 26h24M5 20v6M11 20v6M17 20v6M23 20v6"/></svg></div>
<div class="icon-ring" style="left:572px;top:1540px"><svg width="30" height="30" viewBox="0 0 30 30" fill="none" stroke="var(--green)"><rect x="6" y="3" width="21" height="13"/><path d="M10 7h13M10 10h13M3 14l7-4M3 26h24M5 20v6M11 20v6M17 20v6M23 20v6"/></svg></div>
<div class="icon-ring" style="left:874px;top:1540px"><svg width="30" height="30" viewBox="0 0 30 30" fill="none" stroke="var(--green)"><rect x="6" y="3" width="21" height="13"/><path d="M10 7h13M10 10h13M3 14l7-4M3 26h24M5 20v6M11 20v6M17 20v6M23 20v6"/></svg></div>

<div class="btn dark" style="left:234px;top:1734px;width:127px;height:34px">Get here</div>
<div class="btn dark" style="left:536px;top:1734px;width:129px;height:34px">Get here</div>
<div class="btn dark" style="left:839px;top:1734px;width:127px;height:34px">Get here</div>

<!-- health specialist -->
<div class="photo" style="left:0;top:1850px;width:604px;height:563px;background:linear-gradient(180deg,#1c2a33,#51666f 55%,#8a979b 80%,#3a3f41)" role="img" aria-label="Hiker with backpack standing on a rock above misty mountains"></div>
<section class="abs" style="left:604px;top:1850px;width:596px;height:563px;background:var(--soft)">
  <div class="label" style="left:31px;top:86px">Health specialist</div>
  <div class="heading" style="left:31px;top:108px;width:540px;font-size:29px;line-height:38px">Lorem ipsum dolor sit amet, consectetur adipiscing elit. tempor lorem laoreet.</div>
  <p class="copy" style="left:31px;top:198px;width:528px;line-height:24px">Lorem ipsum dolor sit amet, consectetur adipiscing elit. Etiam sollicitudin ante in purus viverra, vitae tempor lorem laoreet. Vestibulum feugiat, ipsum a euismod finibus, massa nisl tristique lacus, eget pellentesque urna metus a turpis. Nullam eget feugiat enim. Sed id finibus felis. Quisque tincidunt nisl vel risus dapibus, sit amet aliquet justo elementum. Nam non lectus nisi. Nullam eget risus neque.</p>
  <p class="copy" style="left:31px;top:340px;width:528px;line-height:24px">Lorem ipsum dolor sit amet, consectetur adipiscing elit. Etiam sollicitudin ante in purus viverra, vitae tempor lorem laoreet. Vestibulum feugiat, ipsum a euismod finibus, massa nisl tristique lacus, eget pellentesque urna metus a turpis.</p>
  <div class="btn green" style="left:31px;top:443px;width:128px;height:34px">Read more</div>
</section>

<!-- dog school -->
<section class="abs" style="left:0;top:2413px;width:612px;height:562px;background:var(--soft)">
  <div class="label" style="left:70px;top:85px">Dog school</div>
  <div class="heading" style="left:70px;top:106px;width:530px;font-size:29px;line-height:38px">Lorem ipsum dolor sit amet, consectetur adipiscing elit. tempor lorem laoreet.</div>
  <p class="copy" style="left:70px;top:196px;width:524px;line-height:24px">Lorem ipsum dolor sit amet, consectetur adipiscing elit. Etiam sollicitudin ante in purus viverra, vitae tempor lorem laoreet. Vestibulum feugiat, ipsum a euismod finibus, massa nisl tristique lacus, eget pellentesque urna metus a turpis. Nullam eget feugiat enim. Sed id finibus felis. Quisque tincidunt nisl vel risus dapibus, sit amet aliquet justo elementum. Nam non lectus nisi. Nullam eget risus neque.</p>
  <p class="copy" style="left:70px;top:335px;width:524px;line-height:24px">Lorem ipsum dolor sit amet, consectetur adipiscing elit. Etiam sollicitudin ante in purus viverra, vitae tempor lorem laoreet. Vestibulum feugiat, ipsum a euismod finibus, massa nisl tristique lacus, eget pellentesque urna metus a turpis.</p>
  <div class="btn green" style="left:70px;top:444px;width:128px;height:34px">Read more</div>
</section>
<div class="photo" style="left:612px;top:2413px;width:588px;height:562px;background:linear-gradient(120deg,#1f3a40,#2e5157 40%,#7a3d22 65%,#24383b)" role="img" aria-label="Brown dog with red collar looking out of a car window"></div>

<div class="abs" style="left:547px;top:2360px;width:107px;height:107px;background:#fff;border-radius:14px;box-shadow:0 2px 10px rgba(0,0,0,.15);display:flex;align-items:center;justify-content:center">
  <svg width="60" height="60" viewBox="0 0 30 30" fill="none" stroke="var(--green)" stroke-width=".9"><rect x="6" y="3" width="21" height="13"/><path d="M10 7h13M10 10h13M3 14l7-4M3 26h24M5 20v6M11 20v6M17 20v6M23 20v6"/></svg>
</div>

<!-- news -->
<section class="abs" style="left:0;top:2975px;width:1200px;height:640px;background:#fff">
  <div class="label center" style="left:0;top:98px;width:1200px">News</div>
  <div class="heading center" style="left:0;top:120px;width:1200px;font-size:29px">Our Latest News</div>
  <p class="copy center" style="left:400px;top:166px;width:400px;text-align:center;line-height:23px">Lorem ipsum dolor sit amet, consectetur adipiscing elit. Etiam sollicitudin ante in purus viverra, vitae tempor lorem laoreet.</p>
  <svg class="abs" style="left:92px;top:378px" width="28" height="40" viewBox="0 0 28 40"><path d="M22 2L4 20l18 18" fill="none" stroke="var(--dark)" stroke-width="2"/></svg>
  <svg class="abs" style="left:1081px;top:378px" width="28" height="40" viewBox="0 0 28 40"><path d="M6 2l18 18L6 38" fill="none" stroke="var(--green)" stroke-width="2"/></svg>
</section>

<article class="news" style="left:162px">
  <div class="photo" style="left:0;top:0;width:272px;height:143px;background:linear-gradient(180deg,#e9e9e6,#b8b4ab 60%,#4f4a44)" role="img" aria-label="Hands holding glasses at a desk with coffee and phone"></div>
  <div class="news-title">Lorem ipsum dolor sit amet, consectetur.</div>
  <div class="news-meta">▦ May 18, 2021 &nbsp;&nbsp; ▭ 12 comments</div>
  <div class="news-body">Lorem ipsum dolor sit amet, consectetur adipiscing elit. Etiam sollicitudin ante in purus viverra, vitae tempor lorem laoreet.</div>
  <div class="btn green" style="left:91px;top:255px;width:90px;height:26px;font-size:8.5px">Read more</div>
</article>
<article class="news" style="left:465px">
  <div class="photo" style="left:0;top:0;width:272px;height:143px;background:linear-gradient(180deg,#e9e9e6,#b8b4ab 60%,#4f4a44)" role="img" aria-label="Hands holding glasses at a desk with coffee and phone"></div>
  <div class="news-title">Lorem ipsum dolor sit amet, consectetur.</div>
  <div class="news-meta">▦ May 18, 2021 &nbsp;&nbsp; ▭ 12 comments</div>
  <div class="news-body">Lorem ipsum dolor sit amet, consectetur adipiscing elit. Etiam sollicitudin ante in purus viverra, vitae tempor lorem laoreet.</div>
  <div class="btn green" style="left:91px;top:255px;width:90px;height:26px;font-size:8.5px">Read more</div>
</article>
<article class="news" style="left:767px">
  <div class="photo" style="left:0;top:0;width:272px;height:143px;background:linear-gradient(180deg,#e9e9e6,#b8b4ab 60%,#4f4a44)" role="img" aria-label="Hands holding glasses at a desk with coffee and phone"></div>
  <div class="news-title">Lorem ipsum dolor sit amet, consectetur.</div>
  <div class="news-meta">▦ May 18, 2021 &nbsp;&nbsp; ▭ 12 comments</div>
  <div class="news-body">Lorem ipsum dolor sit amet, consectetur adipiscing elit. Etiam sollicitudin ante in purus viverra, vitae tempor lorem laoreet.</div>
  <div class="btn green" style="left:91px;top:255px;width:90px;height:26px;font-size:8.5px">Read more</div>
</article>

<!-- call band -->
<section class="abs" style="left:0;top:3615px;width:1200px;height:188px;background:var(--black)">
  <div class="abs" style="left:258px;top:34px;width:684px;height:120px;background:var(--green);border-radius:12px">
    <svg class="abs" style="left:152px;top:28px" width="74" height="68" viewBox="0 0 74 68" fill="none" stroke="var(--dark)" stroke-width="2.5"><path d="M12 6l10 0 6 14-7 5c4 9 10 15 19 19l5-7 14 6v10c0 4-3 6-7 6C28 58 8 38 6 14c0-5 2-8 6-8z"/><path d="M44 10c8 1 14 7 15 15M44 2c13 1 22 10 23 23"/></svg>
    <div class="abs" style="left:257px;top:39px;color:var(--dark);font-size:19px;text-transform:uppercase">Call to ask any question</div>
    <div class="abs" style="left:257px;top:64px;color:#fff;font-size:36px;font-weight:600">+41 79 512 48 30</div>
  </div>
</section>

<!-- footer -->
<footer class="abs foot" style="left:0;top:3803px;width:1200px;height:335px;background:#fff">
  <div class="logo" style="left:544px;top:53px"><i></i>moluvo.ch</div>
  <h4 style="left:162px;top:121px">QUICK LINKS</h4>
  <ul style="left:162px;top:155px"><li>Home</li><li>About moluvo</li><li>Courses</li><li>Unlock Your Potential</li><li>Contact</li></ul>
  <h4 style="left:335px;top:121px">ADDRESS</h4>
  <ul style="left:335px;top:155px;line-height:27px">
    <li>⌖&nbsp; Lindenweg 27, CH-3900 Brig</li><li>✉&nbsp; info@moluvo.ch</li><li>▯&nbsp; +41 79 512 48 30</li>
  </ul>
  <h4 style="left:641px;top:121px">COMPANY</h4>
  <ul style="left:641px;top:155px"><li>Home</li><li>Terms &amp; Conditions</li><li>Courses</li><li>Online Support</li><li>Contact</li></ul>
  <h4 style="left:843px;top:121px">GET CONNECT</h4>
  <p class="copy" style="left:843px;top:155px;width:196px;font-size:11px;line-height:19px;color:var(--ink)">Lorem ipsum dolor sit amet, consectetur adipiscing elit. Etiam sollicitudin ante in purus viverra, vitae tempor lorem laoreet. Vestibulum feugiat, ipsum a euismod finibus, massa nisl tristique lacus, eget pellentesque urna metus a turpis.</p>
  <div class="abs" style="left:843px;top:283px;display:flex;gap:16px">
    <i style="width:20px;height:20px;border:2px solid var(--green);border-radius:50%;display:block"></i>
    <i style="width:20px;height:20px;border:2px solid var(--green);border-radius:50%;display:block"></i>
    <i style="width:20px;height:20px;border:2px solid var(--green);border-radius:50%;display:block"></i>
    <i style="width:20px;height:20px;border:2px solid var(--green);border-radius:50%;display:block"></i>
  </div>
</footer>
<div class="abs center" style="left:0;top:4138px;width:1200px;height:43px;background:var(--green);color:#fff;font-size:10px;line-height:43px">© 2021 MOLUVO ALL RIGHTS RESERVED</div>

</body>
</html>
```